Canadian Christian Church needs design for new sermon series

A graphic design for our series and an invitation card to invite people to the series. Check design brief for more detailed information. Target audience: young families and young adults. Looking for a creative design that will get people's attention and create interest. See design brief for copy of design purchased for previous series.
Updates
entered Apr 4 incorrectly. Need a week to receive and review designs, and today is Apr 2/19. Thanks!
Target Market(s)
young families and young adults
Colors
Designer to choose colors to be used in the design.
Look and feel

```html
<!DOCTYPE html>
<html lang="en">
<head>
<meta charset="utf-8">
<title>Messy – Sermon Series Invitation</title>
<link href="https://fonts.googleapis.com/css2?family=Anton&family=Roboto+Slab:wght@400;700&family=Montserrat:wght@400;600&display=swap" rel="stylesheet">
<style>
  :root {
    --page: #e4e4e4;
    --band: #3c3330;
    --white: #ffffff;
    --orange: #f7931e;
    --orange-light: #ffd24a;
    --purple: #5b2a86;
    --ink: #3a3431;
    --beige-light: #dcd6c3;
    --beige: #c6bea6;
    --blue: #1f6fc0;
    --link: #f39a2b;
  }
  * { box-sizing: border-box; margin: 0; padding: 0; }
  html, body { width: 1200px; height: 903px; overflow: hidden; background: var(--page); }
  .canvas { position: relative; width: 1200px; height: 903px; }

  .card { position: absolute; overflow: hidden; box-shadow: 0 2px 6px rgba(0,0,0,.25); }

  /* Front */
  .card-front { left: 177px; top: 60px; width: 482px; height: 378px; }
  .hero { position: absolute; inset: 0 0 41px 0;
    background: radial-gradient(ellipse at 45% 65%, #4a4038 0%, #2b2622 45%, #6f6455 100%); }
  .series-title { position: absolute; right: 32px; top: 20px;
    font-family: "Anton", "Oswald", sans-serif; font-weight: 400; font-size: 66px; line-height: 1; letter-spacing: 1px;
    background: linear-gradient(var(--orange-light), var(--orange) 70%);
    -webkit-background-clip: text; background-clip: text; color: transparent;
    -webkit-text-stroke: 2px var(--purple); }
  .series-subtitle { position: absolute; left: 30px; top: 286px; white-space: nowrap;
    font-family: "Roboto Slab", serif; font-weight: 400; font-size: 34px; line-height: 40px; color: var(--orange);
    -webkit-text-stroke: 1px #3a2200; letter-spacing: -0.5px; }
  .tagline-band { position: absolute; left: 0; right: 0; bottom: 0; height: 41px; background: var(--band);
    display: flex; align-items: center; justify-content: center;
    font-family: "Roboto Slab", serif; font-weight: 400; font-size: 22px; color: var(--white); white-space: nowrap; }

  /* Back */
  .card-back { left: 582px; top: 469px; width: 484px; height: 379px;
    background: linear-gradient(160deg, var(--beige-light) 0%, var(--beige) 60%, #d8d1bd 100%); }
  .service-heading { position: absolute; top: 22px; left: 0; right: 0; text-align: center;
    font-family: "Roboto Slab", serif; font-weight: 700; color: var(--ink); font-size: 27px; line-height: 30px; }
  .service-heading .time { display: block; font-family: "Montserrat", sans-serif; font-weight: 600; font-size: 26px; line-height: 32px; }
  .section-title { position: absolute; left: 26px; font-family: "Montserrat", sans-serif; font-weight: 600; font-size: 12px; line-height: 14px; color: var(--ink); white-space: nowrap; }
  .sermons-title { top: 105px; }
  .features-title { top: 247px; }
  .list { position: absolute; left: 28px; list-style: none; font-family: "Montserrat", sans-serif; font-size: 11.5px; color: var(--ink); white-space: nowrap; }
  .list li { height: 14.6px; line-height: 14.6px; display: flex; align-items: center; }
  .list li::before { content: ""; width: 7px; height: 7px; border-radius: 50%; background: var(--blue);
    box-shadow: inset 0 0 0 2px var(--blue), inset 0 0 0 3px #fff; margin-right: 8px; flex: none; }
  .list b { font-weight: 600; margin-right: 4px; }
  .sermons { top: 121px; }
  .features { top: 262px; }
  .values-diagram { position: absolute; left: 294px; top: 94px; width: 172px; height: 166px; border-radius: 40%;
    background: conic-gradient(#f7931e, #1f6fc0, #7a2a9a, #f7931e, #1f6fc0, #f7931e); opacity: .9; }
  .contact-box { position: absolute; left: 0; top: 308px; width: 302px; height: 59px; background: var(--band);
    padding: 5px 0 0 26px; font-family: "Montserrat", sans-serif; font-size: 8.8px; color: var(--white); line-height: 16px; white-space: nowrap; }
  .contact-box .row { display: flex; align-items: center; gap: 4px; height: 16px; }
  .contact-box svg { flex: none; }
  .contact-box a { color: var(--link); text-decoration: none; }
  .church-mark { position: absolute; left: 360px; top: 290px; width: 58px; height: 58px; border-radius: 50%; background: var(--orange); }
  .church-name { position: absolute; left: 314px; top: 351px; width: 150px; text-align: center; white-space: nowrap;
    font-family: "Roboto Slab", serif; font-weight: 400; font-size: 11.5px; line-height: 14px; color: var(--ink); }
</style>
</head>
<body>
<main class="canvas">
  <section class="card card-front">
    <div class="hero" role="img" aria-label="Photo of a cluttered home office with a desk buried in papers"></div>
    <h1 class="series-title">MESSY</h1>
    <p class="series-subtitle">Joining God in the Mess</p>
    <div class="tagline-band">Connecting Young Families to Christ</div>
  </section>

  <section class="card card-back">
    <h2 class="service-heading">THE TIME OF THE SERVICES:<span class="time">Sundays @ 10:30</span></h2>

    <h3 class="section-title sermons-title">Names &amp; Dates of the sermons:</h3>
    <ul class="list sermons">
      <li><b>April 28th:</b> “We Made This Mess”</li>
      <li><b>May 5th:</b> “Bless in the Mess”</li>
      <li><b>May 12th:</b> “Born into the Mess”</li>
      <li><b>May 19th:</b> “Messy Work”</li>
      <li><b>May 26th:</b> “Messy Church”</li>
      <li><b>June 2nd:</b> “Messy Hospitality”</li>
      <li><b>June 9th:</b> TBD</li>
      <li><b>June 16th:</b> “Messy within Boundaries”</li>
    </ul>

    <h3 class="section-title features-title">Features of the service:</h3>
    <ul class="list features">
      <li>Staffed nursery &amp; children’s program every Sunday</li>
      <li>Coffee &amp; snacks</li>
      <li>Everyone welcome</li>
    </ul>

    <div class="values-diagram" role="img" aria-label="Illustration of the church's five core values as interlocking coloured bands"></div>

    <div class="contact-box">
      <div class="row">
        <svg width="9" height="11" viewBox="0 0 10 12"><path d="M5 0a4 4 0 0 1 4 4c0 3-4 8-4 8S1 7 1 4a4 4 0 0 1 4-4z" fill="#f39a2b"/><circle cx="5" cy="4" r="1.5" fill="#3c3330"/></svg>
        118 Birchwood Road East Oakville, ON L6H 2K4
      </div>
      <div class="row">
        <svg width="10" height="10" viewBox="0 0 10 10"><path d="M2 0l2 2.5-1 1.3a6 6 0 0 0 3.2 3.2L7.5 6 10 8l-1.3 1.7C4.5 10 0 5.5.3 1.3z" fill="#f39a2b"/></svg>
        905-555-0147 &nbsp;
        <svg width="10" height="10" viewBox="0 0 10 10"><circle cx="5" cy="5" r="4.5" fill="none" stroke="#f39a2b"/><path d="M.5 5h9M5 .5c-2.5 3-2.5 6 0 9M5 .5c2.5 3 2.5 6 0 9" fill="none" stroke="#f39a2b" stroke-width=".8"/></svg>
        www.maplegrovechurch.ca
      </div>
      <div class="row">Please contact Laura Bennett <a href="#">worship@maplegrovechurch.ca</a></div>
    </div>

    <div class="church-mark"></div>
    <p class="church-name">Maple Grove Family Church</p>
  </section>
</main>
</body>
</html>
```